Food broker, trader, wholesaler, liquidator looking for a 5 pages website

Looking for a 5 pages website design. We are food brokers, traders, wholesaler and closeout buyer working with manufacturers, distributors, importers sell to retailers, food service operators and industrial (ingredients). We help market their products. We are a resource for those who need a solution in the distribution/selling/placement of food on the shelves, kitchens and pantries. Whether we open new accounts with new products or sell short dated inventory, we know where to go and get results.

Target Market(s)

Food manufacturers, food distributors, food brokers

Coding

Coded - Design and coding required

Number of Pages Required

4 page

Font styles to use
Serif

Requirements
Must have
• Food-food production-warehouse-Food packaging-people meeting-trucks-supermarket shelves-

```html
<!DOCTYPE html>
<html lang="en">
<head>
<meta charset="utf-8">
<title>Harborline Provisions</title>
<link rel="stylesheet" href="https://fonts.googleapis.com/css2?family=Merriweather:wght@300;400;700&family=Open+Sans:wght@400;600&display=swap">
<style>
:root{
  --navy:#0c0a4f;
  --navy-text:#15135e;
  --ink:#444;
  --line:#9a9a9a;
  --grey-bg:#e8e8e8;
  --white:#fff;
}
*{box-sizing:border-box;margin:0;padding:0}
html,body{width:1200px;height:3072px;overflow:hidden;background:var(--white)}
body{position:relative;font-family:"Merriweather",Georgia,serif;color:var(--ink)}
.abs{position:absolute}

/* header */
.brand{left:144px;top:14px;display:flex;flex-direction:column;align-items:center;width:176px}
.brand-mark{width:100px;height:76px;border-radius:50%;background:var(--navy)}
.brand-name{margin-top:8px;font-size:13px;font-weight:700;color:var(--navy-text);letter-spacing:.3px;white-space:nowrap}
.phone{right:144px;top:32px;font-size:24px;font-weight:300;color:var(--navy-text);display:flex;align-items:center;gap:8px}
.nav{right:144px;top:97px;display:flex;gap:42px;font-size:15px;font-weight:300;color:#555}
.nav .active{color:var(--navy-text)}

/* hero */
.hero{left:0;top:129px;width:1200px;height:556px;overflow:hidden;
  background:radial-gradient(ellipse at 60% 40%,#d98a4f 0%,#b8703f 30%,#8c8a86 60%,#5a5753 100%)}
.hero-title{left:0;top:222px;width:1200px;text-align:center;font-size:31px;font-weight:700;color:var(--white);text-shadow:0 2px 6px rgba(0,0,0,.5);letter-spacing:.5px}
.hero-arrow{top:222px;width:44px;height:44px;border-radius:50%;background:var(--navy)}
.hero-curve{left:0;bottom:0}

/* sections */
.section-title{left:0;width:1200px;text-align:center;font-size:32px;font-weight:300;color:var(--navy-text)}
.rule{left:560px;width:80px;height:3px;background:var(--navy)}

.step{width:218px;height:144px;border:1px solid var(--line);background:var(--white);display:flex;flex-direction:column;align-items:center}
.step-icon{margin-top:16px;width:70px;height:70px;background:#d6d6dc;border-radius:4px}
.step-label{margin-top:18px;font-size:16px;font-weight:300;color:#555}

.btn{background:var(--navy);color:var(--white);font-size:14px;font-weight:300;display:flex;align-items:center;justify-content:center}

/* about */
.about-photo{left:0;top:1325px;width:600px;height:520px;
  background:linear-gradient(110deg,#6d8a9e 0%,#a7b7a0 30%,#d9c860 60%,#8a6a44 100%)}
.about-panel{left:600px;top:1341px;width:600px;height:481px;background:var(--navy);color:var(--white)}
.about-panel h2{position:absolute;left:40px;top:70px;font-size:32px;font-weight:300}
.about-panel .bar{position:absolute;left:40px;top:130px;width:80px;height:3px;background:var(--white)}
.about-panel .small{position:absolute;left:40px;width:420px;font-family:"Open Sans",Arial,sans-serif;font-size:11.5px;line-height:21px}
.about-panel .lead{position:absolute;left:40px;top:214px;font-family:"Open Sans",Arial,sans-serif;font-size:16px}
.about-panel .outline-btn{position:absolute;left:41px;top:366px;width:112px;height:40px;border:1px solid var(--white);font-size:14px;font-weight:300;display:flex;align-items:center;justify-content:center}

/* services */
.card-photo{top:1998px;width:296px;height:336px}
.card-label{top:2319px;width:280px;height:87px;background:var(--navy);color:var(--white);font-size:23px;font-weight:300;text-align:center;line-height:29px;padding-top:14px}

/* contact */
.contact{left:0;top:2486px;width:1200px;height:464px;background:var(--grey-bg)}
.field{background:var(--white);border:1px solid #d4d4d4;border-radius:3px;font-family:"Open Sans",Arial,sans-serif;font-size:11px;color:#333;padding:12px 14px}

/* footer */
.footer{left:0;top:2950px;width:1200px;height:122px;background:var(--navy)}
.footer-links{left:145px;top:2989px;font-family:"Open Sans",Arial,sans-serif;font-size:11.5px;color:#b9b8e0;word-spacing:2px}
.footer-copy{left:145px;top:3021px;font-family:"Open Sans",Arial,sans-serif;font-size:11.5px;color:#b9b8e0;word-spacing:2px}
.social{top:3000px;width:22px;height:22px;border-radius:50%;background:#6e6cb3}
</style>
</head>
<body>

<header>
  <div class="brand abs">
    <div class="brand-mark"></div>
    <div class="brand-name">HARBORLINE PROVISIONS</div>
  </div>
  <div class="phone abs">
    <svg width="20" height="20" viewBox="0 0 24 24"><path fill="#15135e" d="M6.6 10.8a15.1 15.1 0 0 0 6.6 6.6l2.2-2.2a1 1 0 0 1 1-.25 11.4 11.4 0 0 0 3.6.57 1 1 0 0 1 1 1V20a1 1 0 0 1-1 1A17 17 0 0 1 3 4a1 1 0 0 1 1-1h3.5a1 1 0 0 1 1 1c0 1.25.2 2.45.57 3.57a1 1 0 0 1-.25 1z"/></svg>
    555 014 2290
  </div>
  <nav class="nav abs">
    <span class="active">ABOUT US</span><span>WHAT WE DO</span><span>CONTACT</span><span>GIVING BACK</span>
  </nav>
</header>

<section class="hero abs" role="img" aria-label="Photo of brown eggs moving along a stainless steel processing line">
  <div class="hero-title abs">AENEAN SED QUAM NON SAPIEN FAUCIBUS</div>
  <div class="hero-arrow abs" style="left:51px">
    <svg width="44" height="44" viewBox="0 0 44 44"><path d="M25 14l-8 8 8 8" fill="none" stroke="#fff" stroke-width="3"/></svg>
  </div>
  <div class="hero-arrow abs" style="left:1103px">
    <svg width="44" height="44" viewBox="0 0 44 44"><path d="M19 14l8 8-8 8" fill="none" stroke="#fff" stroke-width="3"/></svg>
  </div>
  <svg class="hero-curve abs" width="1200" height="70" viewBox="0 0 1200 70">
    <path d="M0 70 L0 45 Q600 -40 1200 45 L1200 70 Z" fill="#0c0a4f"/>
    <path d="M0 70 Q600 -10 1200 70 Z" fill="#fff"/>
  </svg>
</section>

<section class="how">
  <h2 class="section-title abs" style="top:757px">HOW IT WORKS</h2>
  <div class="rule abs" style="top:812px"></div>
  <svg class="abs" style="left:0;top:0" width="1200" height="1240">
    <g stroke="#9a9a9a" stroke-width="1" fill="none">
      <path d="M362 912h14M593 912h14M825 912h14"/>
      <path d="M948 984v25H368v22"/>
      <path d="M477 1103h14M709 1103h14"/>
    </g>
  </svg>
  <div class="step abs" style="left:144px;top:840px"><div class="step-icon" role="img" aria-label="Food icon"></div><div class="step-label">1. Food</div></div>
  <div class="step abs" style="left:375px;top:840px"><div class="step-icon" role="img" aria-label="Food production icon"></div><div class="step-label">2. Food Production</div></div>
  <div class="step abs" style="left:607px;top:840px"><div class="step-icon" role="img" aria-label="Warehouse icon"></div><div class="step-label">3. Warehouse</div></div>
  <div class="step abs" style="left:838px;top:840px"><div class="step-icon" role="img" aria-label="Food packaging icon"></div><div class="step-label">4. Food Packaging</div></div>
  <div class="step abs" style="left:260px;top:1031px"><div class="step-icon" role="img" aria-label="Handshake icon"></div><div class="step-label">5. People Meeting</div></div>
  <div class="step abs" style="left:491px;top:1031px"><div class="step-icon" role="img" aria-label="Truck icon"></div><div class="step-label">6. Trucks</div></div>
  <div class="step abs" style="left:723px;top:1031px"><div class="step-icon" role="img" aria-label="Supermarket shelves icon"></div><div class="step-label">7. Supermarket Shelves</div></div>
  <div class="btn abs" style="left:524px;top:1197px;width:152px;height:40px">GET STARTED NOW</div>
</section>

<section class="about">
  <div class="about-photo abs" role="img" aria-label="Photo of a shopper choosing produce from a supermarket shelf"></div>
  <div class="about-panel abs">
    <h2>ABOUT US</h2>
    <div class="bar"></div>
    <p class="small" style="top:155px">Harborline Provisions works with food manufacturers, brand owners, distributors and wholesalers market their products.</p>
    <p class="lead">Retail, Food Service and Industrial ingredients.</p>
    <p class="small" style="top:259px">Founded in 2008, Harborline Provisions started with the distribution of gluten free products understanding the need to provide access to unique flavors and products for the celiac consumers. From this, we expanded into deli, dairy, groceries, frozen and beverages.</p>
    <div class="outline-btn">READ MORE</div>
  </div>
</section>

<section class="services">
  <h2 class="section-title abs" style="top:1915px">WHAT WE DO</h2>
  <div class="rule abs" style="top:1970px"></div>
  <div class="card-photo abs" style="left:144px;background:linear-gradient(160deg,#f2e6dc,#c84a4a 55%,#d3b6a6)" role="img" aria-label="Photo of a red sale sign in a store aisle"></div>
  <div class="card-photo abs" style="left:452px;background:linear-gradient(160deg,#4a4a52,#8a7a5a 50%,#c99a4a)" role="img" aria-label="Photo of a shopper with a grocery basket in an aisle"></div>
  <div class="card-photo abs" style="left:760px;background:linear-gradient(160deg,#c65a4a,#b8b2aa 45%,#8c8c94)" role="img" aria-label="Photo of a shopper pushing a cart past stocked shelves"></div>
  <div class="card-label abs" style="left:152px">SALES &amp;<br>MARKETING</div>
  <div class="card-label abs" style="left:460px">TRADING</div>
  <div class="card-label abs" style="left:767px">CLOSEOUT/EXCESS<br>INVENTORY</div>
</section>

<section class="contact abs">
  <h2 class="section-title abs" style="top:71px">CONTACT US</h2>
  <div class="rule abs" style="top:128px"></div>
  <div class="field abs" style="left:144px;top:155px;width:218px;height:40px">Name</div>
  <div class="field abs" style="left:375px;top:155px;width:218px;height:40px">Company Name</div>
  <div class="field abs" style="left:607px;top:155px;width:218px;height:40px">Email</div>
  <div class="field abs" style="left:838px;top:155px;width:218px;height:40px">Phone</div>
  <div class="field abs" style="left:144px;top:211px;width:912px;height:111px">Message</div>
  <div class="btn abs" style="left:556px;top:345px;width:88px;height:39px">SUBMIT</div>
</section>

<footer class="footer abs"></footer>
<div class="footer-links abs">About Us &nbsp;|&nbsp; What We Do &nbsp;|&nbsp; Contact &nbsp;|&nbsp; Giving Back</div>
<div class="footer-copy abs">Copyright © 2020 Harborline Provisions. All rights reserved.</div>
<div class="social abs" style="left:946px"></div>
<div class="social abs" style="left:990px"></div>
<div class="social abs" style="left:1033px"></div>

</body>
</html>
```